Social Media Graphics - Oakline Push REVISED

Create 6-7 individual social media graphics (square size) to encourage folks to join our online course called:

The Harvest Ledger Circle
How to Launch a Multi-Million Business From Scratch
Sign Up Today!

IMPORTANT: Make the largest and most prominent text on the graphic be: How to Launch a Multi-Million Business From Scratch

For the color scheme of the graphics, let's try a blue color palette; make sure the graphics appeal to both men and women

Make sure each graphic contains 1 of the 3 pics attached (crop pic as needed); and make sure one of the graphics is all TEXT only.

Target Market(s)

men and women looking to start a business

Industry/Entity Type

Entrepreneurship

Colors
0054AA
0677BA
7BADD7
CADEEF
E8F1F8

Requirements
Must have
• All the text and use the 3 pics provided; one graphic can be all text; Simple, modern design that's easy to read

```html
<!DOCTYPE html>
<html lang="en">
<head>
<meta charset="utf-8">
<title>The Harvest Ledger Circle — Sign Up Today</title>
<link rel="stylesheet" href="https://fonts.googleapis.com/css2?family=Anton&family=Michroma&family=Oswald:wght@700&display=swap">
<style>
  :root {
    --sky-top: #1b93d1;
    --sky-mid: #176aa3;
    --sky-deep: #0d426e;
    --ink-pill: #1b2233;
    --ink-panel: #1f1f3e;
    --accent: #3da0dc;
    --white: #ffffff;
  }
  html, body {
    margin: 0;
    padding: 0;
    width: 1200px;
    height: 1200px;
    overflow: hidden;
    background: var(--sky-deep);
  }
  .graphic {
    display: block;
    width: 1200px;
    height: 1200px;
  }
  .brand-line {
    font-family: "Michroma", sans-serif;
    font-weight: 400;
    fill: var(--white);
  }
  .headline {
    font-family: "Anton", "Impact", sans-serif;
    font-weight: 400;
    fill: var(--white);
  }
  .cta {
    font-family: "Oswald", sans-serif;
    font-weight: 700;
    fill: var(--accent);
    letter-spacing: 6px;
  }
</style>
</head>
<body>
<svg class="graphic" viewBox="0 0 1200 1200" xmlns="http://www.w3.org/2000/svg">
  <defs>
    <radialGradient id="sky" cx="600" cy="110" r="900" gradientUnits="userSpaceOnUse">
      <stop offset="0" stop-color="var(--sky-top)"/>
      <stop offset="0.35" stop-color="var(--sky-mid)"/>
      <stop offset="0.7" stop-color="var(--sky-deep)"/>
      <stop offset="1" stop-color="var(--sky-deep)"/>
    </radialGradient>
  </defs>

  <!-- backdrop -->
  <rect class="backdrop" width="1200" height="1200" fill="url(#sky)"/>

  <!-- course name -->
  <g class="course-name">
    <rect x="154" y="100" width="895" height="118" rx="30" fill="var(--white)"/>
    <rect x="154" y="107" width="895" height="112" rx="30" fill="var(--ink-pill)"/>
    <text class="brand-line" x="601" y="192" text-anchor="middle" font-size="62"
          textLength="820" lengthAdjust="spacingAndGlyphs">THE HARVEST LEDGER</text>
    <text class="brand-line" x="590" y="329" text-anchor="middle" font-size="84"
          textLength="760" lengthAdjust="spacing">CIRCLE</text>
  </g>

  <!-- headline panel -->
  <g class="headline-panel">
    <rect x="55" y="371" width="1091" height="652" rx="31" fill="var(--ink-panel)"/>
    <rect x="70" y="388" width="1060" height="618" rx="30" fill="none" stroke="var(--accent)" stroke-width="1.5"/>
    <rect x="75" y="394" width="1050" height="606" rx="26" fill="none" stroke="var(--accent)" stroke-width="1.5"/>

    <text class="headline" x="118" y="604" font-size="196"
          textLength="950" lengthAdjust="spacingAndGlyphs">HOW TO LAUNCH</text>
    <text class="headline" x="117" y="801" font-size="186"
          textLength="952" lengthAdjust="spacingAndGlyphs">A MULTI-MILLION</text>
    <text class="headline" x="113" y="957" font-size="146"
          textLength="943" lengthAdjust="spacingAndGlyphs">BUSINESS FROM SCRATCH</text>
  </g>

  <!-- call to action -->
  <g class="call-to-action">
    <line x1="59" y1="1082" x2="429" y2="1082" stroke="var(--accent)" stroke-width="5"/>
    <line x1="770" y1="1082" x2="1140" y2="1082" stroke="var(--accent)" stroke-width="5"/>
    <text class="cta" x="603" y="1097" text-anchor="middle" font-size="48"
          textLength="302" lengthAdjust="spacingAndGlyphs">SIGN UP TODAY</text>
  </g>
</svg>
</body>
</html>
```